Granite Bureau of Analysis Card Design

I need a business card for the agency I currently am tasked with, which is based in Hartford, CT. GBAN provides, disseminates and obtains intelligence in regards to ongoing criminal investigations throughout the State of CT. The information we obtain and provide, comes to us and is sent out by various Law Enforcement agencies throughout CT.

Industry/Entity Type

Business

Contact Information for Business Card

Officer Lyle P. Harrowby
Bramford Police Department - Eastern Region Intelligence Officer
Granite Bureau of Analysis
4827 Willowmere Ave., Middletown, CT 06457
Work Cell: (555) 318-2694
E-Mail: gban.wd@gbanmail.example

```html
<!DOCTYPE html>
<html lang="en">
<head>
<meta charset="utf-8">
<title>Granite Bureau of Analysis – Business Card</title>
<link rel="stylesheet" href="https://fonts.googleapis.com/css2?family=Michroma&display=swap">
<style>
  :root {
    --page-bg: #e9e7e4;
    --card-white: #ffffff;
    --card-grey: #ececec;
    --brand-red: #b8302a;
    --accent-yellow: #e2cc3c;
    --ink-light: #ffffff;
    --ink-dark: #1d1d1b;
  }
  * { margin: 0; padding: 0; box-sizing: border-box; }
  html, body {
    width: 1200px;
    height: 900px;
    overflow: hidden;
    background: var(--page-bg);
    font-family: "Michroma", "Arial", sans-serif;
  }
  .canvas {
    position: relative;
    width: 1200px;
    height: 900px;
  }
  .business-card {
    position: absolute;
    left: 150px;
    top: 193px;
    width: 900px;
    height: 514px;
    border-radius: 40px;
    overflow: hidden;
    background: linear-gradient(180deg, var(--card-white) 0%, var(--card-grey) 100%);
    box-shadow: 0 10px 30px rgba(0,0,0,0.18);
  }
  .card-waves {
    position: absolute;
    inset: 0;
    width: 100%;
    height: 100%;
  }
  .wave-yellow { fill: var(--accent-yellow); }
  .wave-red { fill: var(--brand-red); }

  .agency-mark {
    position: absolute;
    left: 300px;
    top: 70px;
    width: 200px;
    display: flex;
    flex-direction: column;
    align-items: center;
    gap: 10px;
  }
  .agency-mark__shape {
    width: 26px;
    height: 26px;
    border-radius: 50%;
    background: var(--ink-dark);
  }
  .agency-mark__name {
    font-size: 17px;
    line-height: 1.35;
    color: var(--ink-dark);
    text-align: center;
    text-transform: uppercase;
    letter-spacing: 1px;
  }

  .holder {
    position: absolute;
    right: 400px;
    top: 368px;
    text-align: right;
    color: var(--ink-light);
    font-variant: small-caps;
    letter-spacing: 1px;
    white-space: nowrap;
  }
  .holder__name { font-size: 18px; line-height: 24px; margin-bottom: 4px; }
  .holder__title { font-size: 12px; line-height: 19px; }

  .divider {
    position: absolute;
    left: 518px;
    top: 318px;
    width: 1.5px;
    height: 160px;
    background: var(--ink-light);
  }

  .contact-list {
    position: absolute;
    left: 540px;
    top: 326px;
    list-style: none;
    color: var(--ink-light);
    font-variant: small-caps;
    letter-spacing: 1px;
    font-size: 14px;
    white-space: nowrap;
  }
  .contact-list li {
    display: flex;
    align-items: flex-start;
    gap: 10px;
    line-height: 22px;
    margin-bottom: 8px;
  }
  .contact-list .group-gap { margin-top: 14px; }
  .contact-icon { width: 18px; height: 18px; flex: none; margin-top: 2px; }
  .contact-icon circle.disc { fill: var(--ink-light); }
  .contact-icon .glyph { fill: var(--brand-red); }
  .contact-icon .line { fill: none; stroke: var(--brand-red); stroke-width: 1.4; }
</style>
</head>
<body>
<main class="canvas">
  <section class="business-card" aria-label="Business card">
    <svg class="card-waves" viewBox="0 0 900 514" preserveAspectRatio="none" aria-hidden="true">
      <path class="wave-yellow" d="M0 340 C 240 362, 520 190, 900 100 L900 110 C 520 205, 250 378, 0 362 Z"/>
      <path class="wave-red" d="M0 372 C 260 388, 530 222, 900 122 L900 514 L0 514 Z"/>
    </svg>

    <div class="agency-mark">
      <span class="agency-mark__shape" aria-hidden="true"></span>
      <span class="agency-mark__name">Bramford<br>Police</span>
    </div>

    <div class="holder">
      <p class="holder__name">Officer Lyle P. Harrowby</p>
      <p class="holder__title">Bramford Police Department</p>
      <p class="holder__title">Eastern Region Intelligence Officer</p>
      <p class="holder__title">Granite Bureau of Analysis</p>
    </div>

    <div class="divider" aria-hidden="true"></div>

    <ul class="contact-list">
      <li>
        <svg class="contact-icon" viewBox="0 0 18 18" aria-hidden="true"><circle class="disc" cx="9" cy="9" r="9"/><path class="glyph" d="M6 4.5 L8 7 L7 8.2 C7.6 9.6 8.4 10.4 9.8 11 L11 10 L13.5 12 L12.5 13.5 C8.5 13.2 4.8 9.5 4.5 5.5 Z"/></svg>
        <span>Work Cell: (555) 318-2694</span>
      </li>
      <li>
        <svg class="contact-icon" viewBox="0 0 18 18" aria-hidden="true"><circle class="disc" cx="9" cy="9" r="9"/><rect class="line" x="4" y="5.5" width="10" height="7"/><path class="line" d="M4 5.5 L9 9.5 L14 5.5"/></svg>
        <span>gban.wd@gbanmail.example</span>
      </li>
      <li class="group-gap">
        <svg class="contact-icon" viewBox="0 0 18 18" aria-hidden="true"><circle class="disc" cx="9" cy="9" r="9"/><path class="glyph" d="M9 3.5 C6.6 3.5 5 5.2 5 7.3 C5 10 9 14.5 9 14.5 C9 14.5 13 10 13 7.3 C13 5.2 11.4 3.5 9 3.5 Z"/><circle cx="9" cy="7.4" r="1.5" fill="#ffffff"/></svg>
        <span>4827 Willowmere Ave.,<br>Middletown, CT 06457</span>
      </li>
    </ul>
  </section>
</main>
</body>
</html>
```